Boutique town planning business needs a Business Card design

We need a business card design for a new company called The Zoning Bridgeway. We provide town planning and urban design services to government, business and community groups. We would like to see the designs use the colours in the logo (blue, deep red, green and amber), plenty of white and including black and grey in the writing. The final design should communicate collaboration, creativity and professionalism and that we are approachable.

Industry/Entity Type

Town

```html
<!DOCTYPE html>
<html lang="en">
<head>
<meta charset="utf-8">
<title>The Zoning Bridgeway – Business Card</title>
<link rel="stylesheet" href="https://fonts.googleapis.com/css2?family=Open+Sans:ital,wght@0,400;0,600;0,700;1,400&display=swap">
<style>
  :root {
    --page: #d9dadb;
    --card: #ffffff;
    --ink: #2b2b2b;
    --grey: #6b6b6b;
    --band: #111111;
    --band-edge: #9a9a9a;
    --blue: #2a9fd6;
    --red: #9c3b2c;
    --green: #5aa63c;
    --amber: #f0a020;
  }
  * { margin: 0; padding: 0; box-sizing: border-box; }
  html, body { width: 1200px; height: 772px; overflow: hidden; }
  body {
    background: var(--page);
    font-family: "Open Sans", Arial, sans-serif;
    display: flex;
    align-items: center;
    justify-content: center;
    gap: 40px;
  }
  .card {
    width: 540px;
    height: 309px;
    background: var(--card);
    position: relative;
    box-shadow: 0 6px 18px rgba(0,0,0,0.18);
  }
  .brand {
    display: flex;
    align-items: center;
    gap: 10px;
    color: var(--ink);
    font-weight: 600;
    font-size: 20px;
    letter-spacing: 0.2px;
  }
  .brand-dot {
    width: 44px;
    height: 44px;
    border-radius: 50%;
    background: var(--blue);
    flex: none;
  }
  .card-back {
    display: flex;
    align-items: center;
    justify-content: center;
  }
  .card-front .brand {
    position: absolute;
    top: 44px;
    left: 50%;
    transform: translateX(-50%);
    white-space: nowrap;
  }
  .name-band {
    position: absolute;
    left: 0;
    right: 0;
    top: 126px;
    height: 44px;
    background: var(--band);
    border-top: 4px solid var(--band-edge);
    border-bottom: 4px solid var(--band-edge);
    display: flex;
    align-items: center;
    justify-content: center;
    color: #fff;
    font-size: 17px;
  }
  .name-band .person { font-weight: 700; }
  .name-band .role { font-style: italic; font-weight: 400; margin-left: 6px; }
  .contacts {
    position: absolute;
    left: 28px;
    right: 28px;
    top: 196px;
    list-style: none;
    display: flex;
    flex-wrap: wrap;
    justify-content: center;
    gap: 10px 18px;
    font-size: 11px;
    color: var(--grey);
  }
  .contacts li { display: flex; align-items: center; gap: 5px; }
  .contacts svg { width: 13px; height: 13px; flex: none; }
</style>
</head>
<body>
  <section class="card card-back" aria-label="Business card back">
    <div class="brand"><span class="brand-dot"></span>The Zoning Bridgeway</div>
  </section>

  <section class="card card-front" aria-label="Business card front">
    <div class="brand"><span class="brand-dot"></span>The Zoning Bridgeway</div>
    <div class="name-band"><span class="person">Daniel Reyes |</span><span class="role">Owner / C.E.O</span></div>
    <ul class="contacts">
      <li><svg viewBox="0 0 14 14"><circle cx="7" cy="7" r="7" fill="#555"/><path d="M4.5 3.5l1.5 0 .6 1.8-.9.7a5 5 0 0 0 2.3 2.3l.7-.9 1.8.6 0 1.5c-3.6.3-6.3-2.4-6-6z" fill="#fff"/></svg>555-201-4410</li>
      <li><svg viewBox="0 0 14 14"><circle cx="7" cy="7" r="7" fill="#555"/><path d="M7 3a2.5 2.5 0 0 0-2.5 2.5C4.5 7.5 7 11 7 11s2.5-3.5 2.5-5.5A2.5 2.5 0 0 0 7 3z" fill="#fff"/></svg>Suite # 214, Elm Court, NY 10482</li>
      <li><svg viewBox="0 0 14 14"><circle cx="7" cy="7" r="7" fill="#555"/><circle cx="7" cy="7" r="3.5" fill="none" stroke="#fff"/><path d="M3.5 7h7M7 3.5v7" stroke="#fff"/></svg>www.zoningbridgeway.com</li>
      <li><svg viewBox="0 0 14 14"><circle cx="7" cy="7" r="7" fill="#555"/><path d="M4.5 3.5l1.5 0 .6 1.8-.9.7a5 5 0 0 0 2.3 2.3l.7-.9 1.8.6 0 1.5c-3.6.3-6.3-2.4-6-6z" fill="#fff"/></svg>555-318-2276</li>
      <li><svg viewBox="0 0 14 14"><circle cx="7" cy="7" r="7" fill="#555"/><rect x="4" y="3" width="6" height="8" rx="1" fill="#fff"/></svg>555-467-9053</li>
      <li><svg viewBox="0 0 14 14"><circle cx="7" cy="7" r="7" fill="#555"/><rect x="3.5" y="4.5" width="7" height="5" fill="#fff"/><path d="M3.5 4.5L7 7.3l3.5-2.8" fill="none" stroke="#555" stroke-width=".8"/></svg>hello@zoningbridgeway.com</li>
    </ul>
  </section>
</body>
</html>
```